Puffy Clouds Cotton Candy

Looking for a logo design and business cards to help a 13 year old entrepreneur promote her cotton candy business.
Contact Information for Business Card
Name, Phone & Email
Colors
E54698
E96AAD
F1A4CE
F9D9EA
FCEFF6
A7469A
B969AE
D3A5CF
EDDBEB
F8F0F9
6B429C
8869AF
B7A5CE
E3DAEB
F3F0F8
Requirements
Must have
- A fun feel that is appropriate for a teenage girl selling cotton candy

```html
<!DOCTYPE html>
<html lang="en">
<head>
<meta charset="utf-8">
<title>Puffy Clouds Cotton Candy – Business Card</title>
<link rel="stylesheet" href="https://fonts.googleapis.com/css2?family=Poppins:wght@400;600;700&display=swap">
<style>
  :root {
    --pink: #ff2d8f;
    --pink-soft: #f26aad;
    --pink-light: #f9a4ce;
    --ink: #10131f;
    --black: #000000;
    --white: #ffffff;
    --page: #ffffff;
  }
  * { margin: 0; padding: 0; box-sizing: border-box; }
  html, body {
    width: 1200px; height: 1200px; overflow: hidden;
    background: var(--page);
    font-family: "Poppins", sans-serif;
  }
  .card {
    position: absolute;
    left: 259px;
    width: 690px; height: 394px;
    overflow: hidden;
    box-shadow: 6px 8px 14px rgba(0,0,0,0.22);
  }
  .card--front { top: 172px; background: var(--white); }
  .card--back { top: 708px; background: var(--pink); }

  .card__shapes { position: absolute; inset: 0; }

  .holder-name {
    position: absolute; left: 32px; top: 48px;
    font-weight: 600; font-size: 49px; line-height: 1;
    color: var(--ink); letter-spacing: -0.5px;
  }
  .holder-role {
    position: absolute; left: 34px; top: 101px;
    font-size: 12.5px; font-weight: 400; letter-spacing: 1px;
    color: var(--pink); line-height: 1;
  }
  .holder-rule {
    position: absolute; left: 175px; top: 108px;
    width: 166px; height: 2px; background: var(--pink);
  }
  .contact-list { position: absolute; left: 34px; top: 137px; list-style: none; }
  .contact-item {
    display: flex; align-items: center;
    height: 36px; margin-bottom: 13px;
  }
  .contact-icon {
    width: 36px; height: 36px; border-radius: 50%;
    background: var(--pink);
    display: flex; align-items: center; justify-content: center;
    flex: none;
  }
  .contact-text {
    margin-left: 18px;
    font-size: 14px; line-height: 15px; letter-spacing: 0.9px;
    color: var(--black);
  }

  .brand { position: absolute; text-align: center; }
  .brand__art {
    margin: 0 auto;
    border-radius: 48% 52% 45% 45% / 55% 55% 40% 40%;
    background: radial-gradient(circle at 45% 40%, var(--pink-light), var(--pink-soft) 60%, #e04594);
  }
  .brand__name {
    font-weight: 700; color: var(--white);
    line-height: 1; white-space: nowrap;
  }
  .brand--front { left: 422px; top: 94px; width: 200px; }
  .brand--front .brand__art { width: 126px; height: 140px; }
  .brand--front .brand__name { font-size: 29px; margin-top: 34px; }
  .brand--back { left: 221px; top: 57px; width: 240px; }
  .brand--back .brand__art { width: 148px; height: 184px; }
  .brand--back .brand__name { font-size: 35px; margin-top: 28px; }
</style>
</head>
<body>

<section class="card card--front">
  <svg class="card__shapes" width="690" height="394" viewBox="0 0 690 394">
    <path class="band-black" d="M0 300 H347 L315 394 H0 Z" fill="var(--black)"/>
    <path class="panel-pink" d="M629 0 H690 V394 H315 L398 166 C450 30 560 0 629 0 Z" fill="var(--pink)"/>
  </svg>

  <h1 class="holder-name">Lena Moreau</h1>
  <p class="holder-role">SYSTEMS ENGINEER</p>
  <div class="holder-rule"></div>

  <ul class="contact-list">
    <li class="contact-item">
      <span class="contact-icon">
        <svg width="16" height="16" viewBox="0 0 24 24"><path d="M6.6 10.8a15.1 15.1 0 0 0 6.6 6.6l2.2-2.2c.3-.3.7-.4 1-.2 1.1.4 2.3.6 3.6.6.6 0 1 .4 1 1V20c0 .6-.4 1-1 1A17 17 0 0 1 3 4c0-.6.4-1 1-1h3.5c.6 0 1 .4 1 1 0 1.3.2 2.5.6 3.6.1.3 0 .7-.2 1z" fill="var(--white)"/></svg>
      </span>
      <span class="contact-text">000 0000 0000<br>000 0000 0000</span>
    </li>
    <li class="contact-item">
      <span class="contact-icon">
        <svg width="18" height="18" viewBox="0 0 24 24" fill="none" stroke="var(--white)" stroke-width="1.8"><rect x="3" y="6" width="18" height="13" rx="1.5"/><path d="M3 7l9 7 9-7M3 18l7-6M21 18l-7-6"/></svg>
      </span>
      <span class="contact-text">Lorem Ipsum Is Simply<br>Dummy Text</span>
    </li>
    <li class="contact-item">
      <span class="contact-icon">
        <svg width="16" height="18" viewBox="0 0 24 24"><path d="M12 2a7 7 0 0 0-7 7c0 5 7 13 7 13s7-8 7-13a7 7 0 0 0-7-7zm0 9.5A2.5 2.5 0 1 1 12 6.5a2.5 2.5 0 0 1 0 5z" fill="var(--white)"/></svg>
      </span>
      <span class="contact-text">Lorem Ipsum Is Simply<br>Dummy Text</span>
    </li>
  </ul>

  <div class="brand brand--front">
    <div class="brand__art" role="img" aria-label="Illustration of a pink cotton candy swirl on a cone"></div>
    <p class="brand__name">Puffy Clouds</p>
  </div>
</section>

<section class="card card--back">
  <div class="brand brand--back">
    <div class="brand__art" role="img" aria-label="Illustration of a pink cotton candy swirl on a cone"></div>
    <p class="brand__name">Puffy Clouds</p>
  </div>
</section>

</body>
</html>
```